Velmora Cabinets Letter Head and Email Signature

Hi
I would love a design package for a letterhead, email signature, even update my business card if you like if you can come up with a great idea for my new high end cabinet shop. Velmora Cabinets brings timeless craftsmanship to modern interiors, specializing in high end, custom cabinetry designed for architects and interior designers.

Target Market(s)

high end, luxury market

Industry/Entity Type

cabinet making

Requirements
Must have
• my colours of logo as the theme

```html
<!DOCTYPE html>
<html lang="en">
<head>
<meta charset="utf-8">
<title>Velmora Cabinets – Stationery</title>
<link href="https://fonts.googleapis.com/css2?family=Montserrat:wght@400;500;700&display=swap" rel="stylesheet">
<style>
  :root{
    --green:#4a7c43;
    --ink:#1c1c1c;
    --card-black:#1e1e1e;
    --emboss:#2a2a2a;
    --paper:#ffffff;
    --page:#f4f4f4;
    --rule:#8a8a8a;
    --grey-text:#444444;
    --stage:#a6a6a6;
  }
  *{box-sizing:border-box;margin:0;padding:0}
  html,body{width:1067px;height:1200px;overflow:hidden}
  body{background:var(--stage);font-family:"Montserrat",sans-serif;color:var(--ink);position:relative}
  .piece{position:absolute}
  .wordmark{display:flex;align-items:center;gap:5px;font-family:"Montserrat",sans-serif;font-weight:500;color:var(--green);white-space:nowrap;line-height:1}
  .wordmark .mark-square{display:inline-block;background:currentColor;flex:none}

  /* business cards */
  .card{width:281px;height:160px;border-radius:9px;background:var(--card-black);box-shadow:0 3px 6px rgba(0,0,0,.35)}
  .card-back{left:77px;top:76px;display:flex;align-items:center;justify-content:center}
  .card-back .wordmark{color:var(--emboss);font-size:22px}
  .card-back .mark-square{width:18px;height:18px}
  .card-front{left:77px;top:258px}
  .card-front .wordmark{position:absolute;left:14px;top:73px;font-size:10.5px;gap:4px}
  .card-front .mark-square{width:8px;height:8px}
  .card-divider{position:absolute;left:141px;top:48px;width:1px;height:65px;background:var(--green)}
  .card-details{position:absolute;left:150px;top:46px;color:#fff}
  .card-name{font-weight:700;font-size:11.5px;color:var(--green)}
  .card-title{font-size:7.5px;margin-top:3px}
  .card-contacts{margin-top:9px;font-size:7.5px;line-height:11px;list-style:none}
  .card-contacts li{display:flex;align-items:center;gap:4px}
  .card-contacts svg{width:6px;height:6px;fill:var(--green)}
  .dot{display:inline-block;width:5px;height:5px;border-radius:50%;border:1px solid var(--green)}

  /* letterhead */
  .letterhead{left:381px;top:77px;width:240px;height:340px;background:var(--paper);overflow:hidden}
  .letterhead .wordmark{position:absolute;left:23px;top:18px;font-size:8.5px}
  .letterhead .mark-square{width:6px;height:6px}
  .lh-contacts{position:absolute;right:22px;top:16px;font-size:4px;text-align:right;line-height:6px;list-style:none}
  .lh-recipient{position:absolute;left:23px;top:80px;font-size:4.4px;line-height:6px}
  .lh-recipient small{display:block;font-size:3.3px;line-height:5.5px}
  .lh-body{position:absolute;left:23px;top:122px;width:196px;font-size:3.4px;line-height:5.9px;text-align:justify;color:#333}
  .lh-body p{margin-bottom:5px}
  .lh-closing{position:absolute;left:23px;top:252px;font-size:3.6px;line-height:5px}
  .lh-closing .lh-signer{margin-top:14px;font-size:4.4px}
  .lh-footer{position:absolute;left:0;bottom:0;width:240px;height:9px}

  /* envelopes */
  .envelope{background:var(--paper);box-shadow:0 2px 4px rgba(0,0,0,.2)}
  .envelope-front{left:644px;top:79px;width:355px;height:153px}
  .envelope-front .wordmark{position:absolute;left:9px;top:12px;font-size:10px}
  .envelope-front .mark-square{width:7px;height:7px}
  .envelope-back{left:639px;top:258px;width:357px;height:156px}
  .envelope-back svg{position:absolute;left:0;top:0}
  .envelope-back .wordmark{position:absolute;left:0;right:0;top:24px;justify-content:center;font-size:10px;color:var(--ink)}
  .envelope-back .mark-square{width:7px;height:7px}

  /* notebook */
  .notebook-cover{left:171px;top:467px;width:221px;height:315px;background:var(--card-black);box-shadow:4px 6px 10px rgba(0,0,0,.35);display:flex;align-items:center;justify-content:center}
  .notebook-cover .wordmark{color:var(--emboss);font-size:17px}
  .notebook-cover .mark-square{width:13px;height:13px}
  .notebook-spread{left:458px;top:470px;width:441px;height:311px;display:flex;gap:2px}
  .notebook-page{position:relative;flex:1;background:var(--page);box-shadow:0 2px 4px rgba(0,0,0,.2)}
  .notebook-page .wordmark{position:absolute;left:11px;top:18px;font-size:10px}
  .notebook-page .mark-square{width:7px;height:7px}
  .page-date{position:absolute;right:11px;top:22px;font-size:6.5px;color:var(--grey-text)}
  .page-lines{position:absolute;left:11px;right:11px;top:52px;height:241px;
    background:repeating-linear-gradient(to bottom,var(--rule) 0 1px,transparent 1px 12px)}

  /* email signature */
  .signature{left:184px;top:860px;width:710px;height:256px;background:var(--paper);box-shadow:0 3px 6px rgba(0,0,0,.3)}
  .signature .wordmark{position:absolute;left:40px;top:56px;font-size:25px;gap:10px}
  .signature .mark-square{width:20px;height:20px}
  .sig-person{position:absolute;right:40px;top:42px;text-align:right}
  .sig-name{font-weight:700;font-size:24px;color:var(--green)}
  .sig-title{font-size:16px;color:var(--grey-text);margin-top:4px}
  .sig-contacts{position:absolute;left:40px;bottom:32px;list-style:none;font-size:16.5px;line-height:25px;color:var(--grey-text)}
  .sig-contacts li{display:flex;align-items:center;gap:8px}
  .sig-contacts svg{width:14px;height:14px;fill:var(--green)}
  .sig-social{position:absolute;right:40px;bottom:32px;font-size:16.5px;line-height:25px;color:var(--grey-text);display:flex;align-items:center;gap:6px}
  .sig-social .dot{width:13px;height:13px;border-width:2px}
</style>
</head>
<body>

  <section class="piece card card-back">
    <div class="wordmark"><span class="mark-square"></span>Velmora Cabinets</div>
  </section>

  <section class="piece card card-front">
    <div class="wordmark"><span class="mark-square"></span>Velmora Cabinets</div>
    <div class="card-divider"></div>
    <div class="card-details">
      <div class="card-name">Dorian Calloway</div>
      <div class="card-title">Director Craftsman</div>
      <ul class="card-contacts">
        <li><svg viewBox="0 0 10 10"><path d="M2 1h2l1 2.5-1.2 1a6 6 0 0 0 2.7 2.7l1-1.2L10 7v2a1 1 0 0 1-1 1A9 9 0 0 1 1 2a1 1 0 0 1 1-1z"/></svg>0491 570 156</li>
        <li><svg viewBox="0 0 10 10"><path d="M0 2h10v6H0z"/></svg>info@velmoracabinets.com.au</li>
        <li><span class="dot"></span>@velmora.cabinets</li>
      </ul>
    </div>
  </section>

  <section class="piece letterhead">
    <div class="wordmark"><span class="mark-square"></span>Velmora Cabinets</div>
    <ul class="lh-contacts">
      <li>0491 570 156</li>
      <li>info@velmoracabinets.com.au</li>
      <li>@velmora.cabinets</li>
    </ul>
    <div class="lh-recipient">
      HARRIET QUINN
      <small>Chief Executive Officer<br>City/State, Zip Code</small>
    </div>
    <div class="lh-body">
      <p>Thank you for considering Velmora Cabinets for your upcoming residence. Our workshop builds each piece by hand from selected timbers, with joinery made to last for generations. We would be glad to review your drawings and prepare a detailed proposal for the kitchen and library joinery.</p>
      <p>Every project begins with a site visit and a conversation about finishes, hardware and light. From there we produce shop drawings for your approval before any timber is cut.</p>
      <p>Please let us know a suitable time to meet at our showroom. We look forward to working alongside your design team.</p>
    </div>
    <div class="lh-closing">
      Sincerely,
      <div class="lh-signer">Dorian Calloway</div>
    </div>
    <svg class="lh-footer" viewBox="0 0 240 9" preserveAspectRatio="none">
      <polygon points="0,0 121,0 126,9 0,9" fill="var(--green)"/>
      <polygon points="208,0 240,0 240,9 202,9" fill="var(--ink)"/>
    </svg>
  </section>

  <section class="piece envelope envelope-front">
    <div class="wordmark"><span class="mark-square"></span>Velmora Cabinets</div>
  </section>

  <section class="piece envelope envelope-back">
    <svg width="357" height="156" viewBox="0 0 357 156">
      <path d="M0 0 L12 45 Q16 57 30 57 L327 57 Q341 57 345 45 L357 0" fill="none" stroke="#d2d2d2" stroke-width="1"/>
    </svg>
    <div class="wordmark"><span class="mark-square"></span>Velmora Cabinets</div>
  </section>

  <section class="piece notebook-cover">
    <div class="wordmark"><span class="mark-square"></span>Velmora Cabinets</div>
  </section>

  <section class="piece notebook-spread">
    <div class="notebook-page">
      <div class="wordmark"><span class="mark-square"></span>Velmora Cabinets</div>
      <div class="page-date">Date......./....../.......</div>
      <div class="page-lines"></div>
    </div>
    <div class="notebook-page">
      <div class="wordmark"><span class="mark-square"></span>Velmora Cabinets</div>
      <div class="page-date">Date......./....../.......</div>
      <div class="page-lines"></div>
    </div>
  </section>

  <section class="piece signature">
    <div class="wordmark"><span class="mark-square"></span>Velmora Cabinets</div>
    <div class="sig-person">
      <div class="sig-name">Dorian Calloway</div>
      <div class="sig-title">Director Craftsman</div>
    </div>
    <ul class="sig-contacts">
      <li><svg viewBox="0 0 10 10"><path d="M2 1h2l1 2.5-1.2 1a6 6 0 0 0 2.7 2.7l1-1.2L10 7v2a1 1 0 0 1-1 1A9 9 0 0 1 1 2a1 1 0 0 1 1-1z"/></svg>0491 570 156</li>
      <li><svg viewBox="0 0 10 10"><path d="M0 2h10v6H0z"/><path d="M0 2l5 3.5L10 2" fill="none" stroke="#fff" stroke-width="0.8"/></svg>info@velmoracabinets.com.au</li>
    </ul>
    <div class="sig-social">@velmora.cabinets <span class="dot"></span></div>
  </section>

</body>
</html>
```